Business card for Luxury Portable Restroom Trailer company

We are a Luxury Portable Restroom Trailer Company Called FALCRIDGE HIRES. Based in Orange County California. We provide portable restroom trailers for events, such as, Weddings, Concerts, Charity events, Sporting events, Tournaments, Corporate events, ect. We rent and Sell the Luxury restrooms. Our colors are white, grey, and Orange. As you will see in the logo we uploaded.
There are 2 people in the company so the names and titles will change for the 3 people but card will remain the same. Here is the information for each Person: Dwight Penner CFO 555 318-0476
next Person: Leon Marchetti VP 555 318-0476
Next Person: Owen Marchetti CEO 555 318-0476
Information to include on the card: Luxury Restroom Trailers Rental and Sales. Weddings, Concerts, Charity, Sporting and Corp. Events.

```html
<!DOCTYPE html>
<html lang="en">
<head>
<meta charset="utf-8">
<title>Falcridge Hires — Business Card</title>
<link href="https://fonts.googleapis.com/css2?family=Montserrat:wght@400;500;700;800&display=swap" rel="stylesheet">
<style>
  :root {
    --orange: #d24a15;
    --charcoal: #2b2d30;
    --grey-text: #3f4246;
    --paper: #fbfbfa;
    --backdrop: #d2d5d5;
  }
  * { box-sizing: border-box; margin: 0; padding: 0; }
  html, body { width: 1200px; height: 829px; overflow: hidden; }
  body {
    background: var(--backdrop);
    font-family: "Montserrat", sans-serif;
    display: flex;
    align-items: center;
    justify-content: center;
    gap: 40px;
  }
  .card {
    position: relative;
    width: 540px;
    height: 309px;
    background: var(--paper);
    box-shadow: 0 0 0 1px rgba(0,0,0,0.04), 0 3px 0 var(--orange), 0 10px 24px rgba(0,0,0,0.12);
    overflow: hidden;
  }

  /* wordmark */
  .wordmark {
    display: flex;
    align-items: center;
    gap: 10px;
    color: var(--orange);
    font-weight: 800;
    letter-spacing: 0.04em;
    line-height: 1;
  }
  .wordmark-square {
    width: 0.8em;
    height: 0.8em;
    background: var(--orange);
    flex: none;
  }

  /* front */
  .card-front .wordmark {
    position: absolute;
    top: 36px;
    left: 40px;
    font-size: 26px;
  }
  .person {
    position: absolute;
    top: 104px;
    left: 40px;
    padding-left: 18px;
  }
  .person::before {
    content: "";
    position: absolute;
    left: 0;
    top: 2px;
    width: 7px;
    height: 38px;
    background: var(--orange);
  }
  .person-name {
    color: var(--orange);
    font-weight: 700;
    font-size: 20px;
    letter-spacing: 0.05em;
    text-transform: uppercase;
  }
  .person-title {
    color: var(--grey-text);
    font-size: 13px;
    font-weight: 500;
    margin-top: 2px;
  }
  .contacts {
    position: absolute;
    top: 186px;
    left: 40px;
    list-style: none;
    color: var(--grey-text);
    font-size: 13px;
  }
  .contacts li {
    display: flex;
    align-items: center;
    gap: 9px;
    margin-bottom: 9px;
  }
  .contacts svg { width: 11px; height: 11px; fill: var(--orange); flex: none; }
  .emblem {
    position: absolute;
    right: 36px;
    top: 50%;
    transform: translateY(-50%);
    width: 200px;
    height: 200px;
  }

  /* back */
  .card-back {
    display: flex;
    flex-direction: column;
    align-items: center;
    justify-content: center;
    text-align: center;
  }
  .card-back .wordmark { font-size: 36px; }
  .tagline {
    margin-top: 30px;
    color: var(--orange);
    font-size: 14px;
    font-weight: 500;
    letter-spacing: 0.03em;
  }
  .events {
    margin-top: 6px;
    color: var(--grey-text);
    font-size: 14px;
    letter-spacing: 0.03em;
  }
</style>
</head>
<body>

  <section class="card card-front">
    <div class="wordmark"><span class="wordmark-square"></span>FALCRIDGE HIRES</div>

    <div class="person">
      <p class="person-name">Owen Marchetti</p>
      <p class="person-title">CEO</p>
    </div>

    <ul class="contacts">
      <li>
        <svg viewBox="0 0 24 24" aria-hidden="true"><path d="M6.6 10.8a15.1 15.1 0 0 0 6.6 6.6l2.2-2.2a1 1 0 0 1 1-.25 11.4 11.4 0 0 0 3.6.57 1 1 0 0 1 1 1V20a1 1 0 0 1-1 1A17 17 0 0 1 3 4a1 1 0 0 1 1-1h3.5a1 1 0 0 1 1 1c0 1.25.2 2.45.57 3.6a1 1 0 0 1-.25 1z"/></svg>
        555 318-0476
      </li>
      <li>
        <svg viewBox="0 0 24 24" aria-hidden="true"><path d="M2 5h20v14H2zm2 2v.5l8 5 8-5V7l-8 5z"/></svg>
        owen@falcridgehires.com
      </li>
      <li>
        <svg viewBox="0 0 24 24" aria-hidden="true"><circle cx="12" cy="12" r="10"/></svg>
        www.falcridgehires.com
      </li>
    </ul>

    <svg class="emblem" viewBox="0 0 200 200" aria-hidden="true">
      <circle cx="100" cy="100" r="92" fill="none" stroke="var(--orange)" stroke-width="9"/>
    </svg>
  </section>

  <section class="card card-back">
    <div class="wordmark"><span class="wordmark-square"></span>FALCRIDGE HIRES</div>
    <p class="tagline">Luxury Restroom Trailers Rental and Sales</p>
    <p class="events">Weddings | Concerts | Charity | Sporting | Corp</p>
  </section>

</body>
</html>
```